Willow Creek Gatherings Event Planning in need of a design!!

Event Planning company, does a variety of events. I like simple more rustic designs focused on almond blossoms. We are based out of Northern California, the heart of almond country. I would like to see colors in light pinks, beige, light browns, whites or creams. the final design should communicate rustic simplicity. Below are some pictures of Almond blossoms and design ideas I prefer the one called Tulip Grove. Thanks

Target Market(s)

Women in the mid twenties and older. They should be in the upper middle class in need of an amazing party design and coordinator

Industry/Entity Type

Event Planning

Contact Information for Business Card

Maren Lockwood 530-624-0295almondbaffairs@gmail.comalmondblossomaffairs.com

Font styles to use
Other font styles liked:
• Amatic SC

Requirements
Must have
• almond blossom
• my information
• simplicity
Nice to have
• rustic design
• vintage feel
• whimsical
Should not have
• i like pink but not over the top

```html
<!DOCTYPE html>
<html lang="en">
<head>
<meta charset="utf-8">
<title>Maren Lockwood – Business Cards</title>
<link rel="stylesheet" href="https://fonts.googleapis.com/css2?family=Playball&family=Arimo:wght@400&display=swap">
<style>
  :root {
    --mint: #b4e0c6;
    --mint-text: #97cfae;
    --white: #ffffff;
    --canvas: #efebe4;
    --petal-white: #f7f4f1;
    --petal-pink: #e9c9c6;
    --petal-blush: #d98f86;
    --leaf: #8fa877;
    --bark: #7a6a5c;
    --sky: #cfdcea;
    --grass: #7fa35c;
    --path-beige: #d8d0c2;
    --path-shade: #a99d8c;
  }
  * { margin: 0; padding: 0; box-sizing: border-box; }
  html, body { width: 1200px; height: 676px; overflow: hidden; }
  body {
    background: var(--canvas);
    display: flex;
    align-items: center;
    justify-content: center;
    gap: 60px;
  }
  .card {
    position: relative;
    width: 500px;
    height: 286px;
    background: var(--white);
    overflow: hidden;
    box-shadow: 0 6px 18px rgba(80, 60, 40, 0.14);
  }

  /* Front */
  .front-photo {
    position: absolute;
    left: 0; top: 0;
    width: 262px; height: 246px;
    background:
      radial-gradient(circle at 30% 40%, var(--petal-white) 0%, var(--petal-pink) 18%, transparent 34%),
      radial-gradient(circle at 62% 24%, var(--petal-white) 0%, var(--petal-pink) 12%, transparent 24%),
      radial-gradient(circle at 45% 78%, var(--petal-white) 0%, var(--petal-blush) 10%, transparent 26%),
      linear-gradient(160deg, var(--leaf) 0%, #b9c2ac 45%, var(--bark) 110%);
    clip-path: polygon(0 0, 100% 0, 72% 100%, 0 100%);
  }
  .front-info {
    position: absolute;
    left: 225px; right: 14px; top: 20px;
    display: flex;
    flex-direction: column;
    align-items: center;
    color: var(--mint-text);
    font-family: "Arimo", Arial, sans-serif;
  }
  .brand {
    display: flex;
    flex-direction: column;
    align-items: center;
  }
  .brand-circle {
    width: 76px; height: 76px;
    border-radius: 50%;
    background: var(--mint);
  }
  .brand-name {
    font-family: "Playball", cursive;
    font-size: 34px;
    line-height: 1.1;
    color: var(--mint-text);
    margin-top: 2px;
    white-space: nowrap;
  }
  .contact-name {
    font-size: 17px;
    letter-spacing: 1px;
    margin-top: 8px;
  }
  .contact-line {
    font-size: 14px;
    margin-top: 5px;
    white-space: nowrap;
  }
  .web-band {
    position: absolute;
    left: 0; right: 0; bottom: 0;
    height: 40px;
    background: var(--mint);
    color: var(--white);
    font-family: "Arimo", Arial, sans-serif;
    font-size: 17px;
    display: flex;
    align-items: center;
    padding-left: 34px;
  }

  /* Back */
  .back-photo {
    position: absolute;
    inset: 0;
    background:
      radial-gradient(ellipse at 85% 30%, var(--petal-white) 0%, var(--petal-pink) 20%, transparent 45%),
      linear-gradient(200deg, transparent 55%, var(--bark) 100%),
      linear-gradient(180deg, var(--sky) 0%, #e6e4df 30%, var(--grass) 50%, var(--path-beige) 70%, var(--path-shade) 100%);
  }
  .name-band {
    position: absolute;
    left: 0; right: 0; top: 26px;
    height: 112px;
    background: var(--mint);
    display: flex;
    align-items: center;
    justify-content: center;
    border-top: 3px solid var(--white);
    border-bottom: 3px solid var(--white);
  }
  .band-name {
    font-family: "Playball", cursive;
    font-size: 56px;
    color: var(--white);
    white-space: nowrap;
  }
</style>
</head>
<body>
  <section class="card card-front">
    <div class="front-photo" role="img" aria-label="Photograph of white almond blossoms with pink centres on a branch"></div>
    <div class="front-info">
      <div class="brand">
        <div class="brand-circle"></div>
        <div class="brand-name">Maren Lockwood</div>
      </div>
      <p class="contact-name">MAREN LOCKWOOD</p>
      <p class="contact-line">530-817-4362</p>
      <p class="contact-line">willowcgather@mailbox.test</p>
    </div>
    <div class="web-band">willowcreekgatherings.test</div>
  </section>

  <section class="card card-back">
    <div class="back-photo" role="img" aria-label="Photograph of an almond orchard row in bloom with petals covering the path"></div>
    <div class="name-band">
      <span class="band-name">Maren Lockwood</span>
    </div>
  </section>
</body>
</html>
```